Upscale business cards needed for Board of Directors

We need professional business cards created for members of our family business Board of Directors. We would like these relatively simple and straightforward, but also with a unique element to set them apart. Probably stick with neutral and simple colors - white, grey etc. We need space for the traditional elements, including name, title, address, email/phone number. And we will be creating several from this template so it needs to be template that is easy to switch information in and out of.
Business
See description

```html
<!DOCTYPE html>
<html lang="en">
<head>
<meta charset="utf-8">
<title>Harborline Holdings – Business Card</title>
<link href="https://fonts.googleapis.com/css2?family=Open+Sans:wght@400;600;700&display=swap" rel="stylesheet">
<style>
  :root {
    --page: #ececea;
    --gold: #bcab84;
    --gold-light: #c8b994;
    --gold-faint: #ad9c76;
    --ink: #1e1d1e;
    --white: #ffffff;
    --muted: #e6e6e6;
  }
  * { margin: 0; padding: 0; box-sizing: border-box; }
  html, body {
    width: 1200px; height: 900px; overflow: hidden;
    background: var(--page);
    font-family: "Open Sans", Arial, sans-serif;
  }
  .sheet {
    width: 1200px; height: 900px;
    display: flex; flex-direction: column; align-items: center; justify-content: center;
    gap: 48px;
  }
  .card {
    width: 640px; height: 366px; position: relative; overflow: hidden;
    box-shadow: 0 10px 28px rgba(0,0,0,.18);
  }

  /* Back side */
  .card--back { background: var(--gold); }
  .card--back .band {
    position: absolute; left: 0; right: 0; top: 123px; height: 120px;
    background: var(--gold-light);
  }
  .watermark {
    position: absolute; left: 0; right: 0;
    font-size: 46px; font-weight: 700; white-space: nowrap;
    color: var(--gold-faint); opacity: .55; text-align: center;
  }
  .watermark--top { top: 8px; }
  .watermark--bottom { top: 250px; }
  .card--back .company-name {
    position: absolute; left: 0; right: 0; top: 158px;
    text-align: center; color: var(--white); font-size: 40px;
  }

  /* Shared company name */
  .company-name { font-weight: 700; line-height: 1.2; white-space: nowrap; }

  /* Front side */
  .card--front { background: var(--white); }
  .card--front .company-name {
    position: absolute; right: 44px; top: 74px;
    color: var(--ink); font-size: 40px;
  }
  .info-panel {
    position: absolute; left: 0; right: 0; bottom: 0; height: 168px;
    background: var(--ink); color: var(--white);
  }
  .person { position: absolute; left: 36px; top: 28px; }
  .person .name { font-size: 22px; font-weight: 700; }
  .person .title { font-size: 15px; margin-top: 2px; color: var(--muted); }
  .address { position: absolute; left: 36px; top: 100px; font-size: 16px; line-height: 1.3; }
  .contacts {
    position: absolute; right: 28px; top: 24px; list-style: none;
    font-size: 13px; text-align: right;
  }
  .contacts li { display: flex; align-items: center; justify-content: flex-end; gap: 8px; margin-bottom: 7px; }
  .contacts svg { width: 12px; height: 12px; fill: var(--white); }
</style>
</head>
<body>
<main class="sheet">

  <section class="card card--back" aria-label="Card back">
    <div class="band"></div>
    <p class="watermark watermark--top" aria-hidden="true">Harborline Holdings</p>
    <p class="watermark watermark--bottom" aria-hidden="true">Harborline Holdings</p>
    <p class="company-name">Harborline Holdings</p>
  </section>

  <section class="card card--front" aria-label="Card front">
    <p class="company-name">Harborline Holdings</p>
    <div class="info-panel">
      <div class="person">
        <p class="name">Daniel Mercer</p>
        <p class="title">Managing Director</p>
      </div>
      <p class="address">12345, Address Goes Here<br>Country Name, 123456</p>
      <ul class="contacts">
        <li>(021)-555-0142
          <svg viewBox="0 0 24 24" aria-hidden="true"><path d="M6.6 10.8a15 15 0 0 0 6.6 6.6l2.2-2.2c.3-.3.7-.4 1-.2 1.1.4 2.3.6 3.6.6.6 0 1 .4 1 1V20c0 .6-.4 1-1 1A17 17 0 0 1 3 4c0-.6.4-1 1-1h3.5c.6 0 1 .4 1 1 0 1.3.2 2.5.6 3.6.1.3 0 .7-.2 1z"/></svg>
        </li>
        <li>info@harborline.com
          <svg viewBox="0 0 24 24" aria-hidden="true"><path d="M2 5h20v14H2z M2 5l10 8 10-8" stroke="#1e1d1e" stroke-width="2"/></svg>
        </li>
        <li>www.harborline.com
          <svg viewBox="0 0 24 24" aria-hidden="true"><circle cx="12" cy="12" r="10"/></svg>
        </li>
      </ul>
    </div>
  </section>

</main>
</body>
</html>
```